Plate of the Raven: Half-Page Magazine Ad

advertisement in a travel magazine for a casual/fine dining restaurant in the heart of Kestrel Bay, Norland
Needs to say that it is located in the Stonefield Hotel, 247 Larch Avenue.

Northern inspired cuisine
plateoftheraven.example

Don't need to use all the pictures

Dimensions: ad is a half-page, dimensions are 7.25" x 4.8".

Target Market(s)

Upscale dining, corporate travellers

Industry/Entity Type

Restaurant

Colors
0054AA
0677BA
7BADD7
CADEEF
E8F1F8
0094D4
00A9DD
6FCCEA
C7EBF8
E9F6FB
00AB8E
00BBA5
67D7C9
C6EFE9
E9F9F6

Requirements
Must have
• Restaurant logo
Nice to have
• Simple, clean design with upscale feel

```html
<!DOCTYPE html>
<html lang="en">
<head>
<meta charset="utf-8">
<title>Plate of the Raven – Half-Page Ad</title>
<link href="https://fonts.googleapis.com/css2?family=Montserrat:wght@400;500;600&display=swap" rel="stylesheet">
<style>
  :root {
    --brand-blue: #1c52a0;
    --ink-grey: #7a7a7a;
    --ink-dark: #2b2b2b;
    --paper: #f4f5f6;
    --wave-light: #eceef0;
    --wave-mid: #dfe2e5;
    --stage: #ffffff;
    --food-warm: #d9772f;
    --food-deep: #a8461c;
    --food-green: #5f9a3a;
  }
  html, body {
    margin: 0;
    padding: 0;
    width: 1200px;
    height: 862px;
    overflow: hidden;
    background: var(--stage);
  }
  .ad {
    position: absolute;
    left: 20px;
    top: 47px;
    width: 1160px;
    height: 768px;
    overflow: hidden;
    font-family: "Montserrat", sans-serif;
  }
  .ad__backdrop {
    position: absolute;
    inset: 0;
    background: linear-gradient(160deg, var(--paper) 0%, var(--wave-light) 50%, var(--wave-mid) 100%);
  }
  .ad__dish {
    position: absolute;
    left: 0;
    top: 52px;
    width: 476px;
    height: 665px;
    border-radius: 0 46% 40% 0 / 0 30% 40% 0;
    background: radial-gradient(ellipse at 45% 40%, var(--food-green) 0%, var(--food-warm) 42%, var(--food-deep) 100%);
  }
  .brand-name {
    position: absolute;
    left: 684px;
    top: 118px;
    margin: 0;
    font-weight: 600;
    font-size: 40px;
    line-height: 48px;
    letter-spacing: 1px;
    text-transform: uppercase;
    color: var(--ink-dark);
  }
  .info__lead,
  .info__city,
  .info__address,
  .info__cuisine,
  .info__url {
    position: absolute;
    margin: 0;
    left: 684px;
    letter-spacing: 0.5px;
    text-transform: uppercase;
    font-weight: 500;
  }
  .info__lead,
  .info__cuisine {
    font-size: 20px;
    line-height: 24.5px;
    color: var(--ink-grey);
  }
  .info__lead { top: 308px; }
  .info__city {
    top: 410px;
    font-size: 38px;
    line-height: 44px;
    color: var(--brand-blue);
  }
  .info__address {
    top: 500px;
    left: 672px;
    right: 0;
    height: 70px;
    box-sizing: border-box;
    padding: 11px 0 0 12px;
    background: var(--brand-blue);
    color: #fff;
    font-size: 20px;
    line-height: 24px;
  }
  .info__cuisine { top: 590px; }
  .info__url {
    top: 686px;
    font-size: 20px;
    line-height: 24px;
    letter-spacing: 2px;
    text-transform: none;
    color: var(--brand-blue);
  }
</style>
</head>
<body>
  <section class="ad">
    <div class="ad__backdrop" role="img" aria-label="Light grey flowing wave pattern background"></div>
    <div class="ad__dish" role="img" aria-label="Photo of a plated dish topped with fresh microgreens and shaved cheese"></div>

    <h1 class="brand-name">Plate<br>of the<br>Raven</h1>

    <p class="info__lead">Fine dining<br>restaurant<br>in the<br>heart of</p>
    <p class="info__city">Kestrel Bay,<br>Norland</p>
    <p class="info__address">Stonefield Hotel,<br>247 Larch Avenue</p>
    <p class="info__cuisine">Northern<br>inspired<br>cuisine</p>
    <p class="info__url">plateoftheraven.example</p>
  </section>
</body>
</html>
```